Bork Ventures, Inc. Website redesign

Revamp the website, it is old and outdated. www.borkventuresinc.example

Target Market(s)

Information Technology Consulting and Staffing

Coding

Coded - Design and coding required

Number of Pages Required

5+ page

Colors

Designer to choose colors to be used in the design.

Requirements
Must have
• Outlined text boxes just like from the Tolvane.example site. A clean look

```html
<!DOCTYPE html>
<html lang="en">
<head>
<meta charset="utf-8">
<title>Bork Ventures, Inc. – Website Redesign</title>
<link href="https://fonts.googleapis.com/css2?family=Rajdhani:wght@400;500;600;700&family=Jost:wght@300;400;500&family=Archivo+Black&display=swap" rel="stylesheet">
<style>
:root{
  --brand:#9e1c34;
  --body:#676767;
  --ink:#2b2b2b;
  --sheet:#eef0f3;
  --panel:#f4f4f4;
  --footer:#24262a;
  --footer-text:#b9bbbf;
  --social:#1e56b8;
  --thanks:#a3a3a3;
}
*{box-sizing:border-box;margin:0;padding:0}
html,body{width:1200px;height:4874px;overflow:hidden;background:#fff}
body{position:relative;font-family:"Jost",sans-serif;color:var(--body)}
.abs{position:absolute}
.head{font-family:"Rajdhani",sans-serif;font-weight:700;color:var(--ink);text-transform:uppercase}
.center{text-align:center}
.btn{position:absolute;background:var(--brand);color:#fff;font-family:"Rajdhani",sans-serif;font-weight:600;text-transform:uppercase;text-align:center;letter-spacing:.3px}
.photo{position:absolute}
.tiny{font-size:6px;line-height:8.5px}
.small{font-size:7.5px;line-height:11px}

/* style guide */
.sheet-top{position:absolute;left:0;top:0;width:1200px;height:880px;background:var(--sheet)}
.guide-label{position:absolute;font-family:"Rajdhani",sans-serif;font-weight:700;font-size:16px;color:var(--ink);text-transform:uppercase}
.guide-note{position:absolute;font-size:10px;color:var(--body)}
.guide-rule{position:absolute;top:10px;width:1px;height:236px;background:#d6d9de}
.swatch{position:absolute}

/* brand lockup */
.brandmark{position:absolute;display:flex;align-items:center;gap:10px;white-space:nowrap}
.brandmark .box{background:var(--brand)}
.brandmark .name{font-family:"Rajdhani",sans-serif;font-weight:700;color:var(--ink);text-transform:uppercase}
.tagline{position:absolute;font-family:"Jost",sans-serif;font-weight:300;font-variant:small-caps;color:#6d6d6d;white-space:nowrap}

/* page frames */
.page{position:absolute;background:#fff;overflow:hidden;box-shadow:0 1px 8px rgba(0,0,0,.16)}
.section-tag{position:absolute;background:var(--brand);color:#fff;font-family:"Rajdhani",sans-serif;font-weight:600;font-size:27px;line-height:49px;padding-left:14px}
.nav{position:absolute;display:flex;font-family:"Rajdhani",sans-serif;font-weight:600;font-size:6.5px;color:#555;text-transform:uppercase}
.nav .on{color:var(--brand)}
.footer{position:absolute;left:0;background:var(--footer);color:var(--footer-text)}
.foot-head{position:absolute;font-family:"Rajdhani",sans-serif;font-weight:700;color:#fff;text-transform:uppercase}
.foot-list{position:absolute;list-style:none;color:var(--footer-text)}
.field{position:absolute;border:1px solid #4a4d52;color:#777;padding-left:6px}
.social{position:absolute;background:var(--social);color:#fff;font-family:"Rajdhani",sans-serif;font-weight:600;text-transform:uppercase;text-align:center}
.social-word{position:absolute;font-family:"Rajdhani",sans-serif;font-weight:600;color:#d0d2d5;text-transform:uppercase;text-align:center}
.thanks{position:absolute;left:47px;top:4240px}
</style>
</head>
<body>

<!-- ============ STYLE GUIDE ============ -->
<div class="sheet-top"></div>

<div class="guide-label" style="left:95px;top:24px">Color Pallet</div>
<div class="swatch" style="left:95px;top:66px;width:74px;height:44px;background:var(--brand)"></div>
<div class="guide-note" style="left:110px;top:116px">#9E1C34</div>
<div class="guide-label" style="left:95px;top:154px">Font</div>
<div class="guide-note" style="left:95px;top:181px;font-weight:500">Rajdhani | Jost Light</div>

<div class="guide-rule" style="left:470px"></div>
<div class="guide-rule" style="left:867px"></div>

<div class="guide-label" style="left:536px;top:24px">Font Style</div>
<div class="abs head" style="left:536px;top:68px;font-size:18px;font-weight:500">H1:</div>
<div class="guide-note" style="left:536px;top:88px">Rajdhani Regular 25</div>
<div class="guide-note" style="left:681px;top:60px;line-height:14px">Body Font Style<br>Jost Light 18</div>
<div class="abs head" style="left:536px;top:124px;font-size:26px">H2:</div>
<div class="guide-note" style="left:536px;top:155px;font-weight:500">Rajdhani Bold 50</div>

<div class="guide-label" style="left:945px;top:24px">Body Font Color</div>
<div class="swatch" style="left:945px;top:68px;width:72px;height:42px;background:var(--body)"></div>
<div class="guide-note" style="left:960px;top:117px">#676767</div>
<div class="guide-label" style="left:945px;top:147px">CTA Button Style</div>
<div class="btn" style="left:946px;top:178px;width:80px;height:23px;font-size:10px;line-height:23px">Read More</div>

<!-- brand lockup -->
<div class="brandmark" style="left:326px;top:302px">
  <span class="name" style="font-size:36px;line-height:44px;letter-spacing:1px">Bork Ventures</span>
  <span class="box" style="width:28px;height:28px"></span>
</div>
<div class="tagline" style="left:620px;top:308px;font-size:26px">Insight Trust Outcomes</div>

<!-- flat desktop screen -->
<div class="page" style="left:255px;top:411px;width:691px;height:441px;box-shadow:none">
  <div class="brandmark" style="left:56px;top:14px;gap:4px">
    <span class="name" style="font-size:12px">Bork Ventures</span><span class="box" style="width:8px;height:8px"></span>
  </div>
  <div class="tagline" style="left:152px;top:15px;font-size:8px">Insight Trust Outcomes</div>
  <div class="abs" style="right:56px;top:11px;font-size:5px;color:#555">Call Us: 555-014-2290 &nbsp; Mail Us: info@borkventuresinc.example</div>
  <div class="nav" style="left:365px;top:27px;gap:20px;font-size:5.5px"><span class="on">Home</span><span>About Us</span><span>Services</span><span>Strategy</span><span>IT News</span><span>Contact Us</span></div>
  <div class="photo" role="img" aria-label="Close-up photo of a network switch with patch cables" style="left:0;top:39px;width:691px;height:340px;background:linear-gradient(135deg,#8b9185 0%,#cfd2c6 35%,#6f7468 60%,#2f3530 100%)"></div>
  <div class="abs head" style="left:421px;top:152px;font-size:12px;color:#fff;font-weight:600">Bringing Thought</div>
  <div class="abs head" style="left:421px;top:167px;font-size:34px;color:var(--brand);line-height:36px">Leadership</div>
  <div class="abs head" style="left:421px;top:212px;font-size:9px;color:#fff;letter-spacing:3px;font-weight:600">— Quality to every project</div>
  <div class="abs head center" style="left:0;width:691px;top:408px;font-size:16px">Our Services</div>
</div>

<!-- flat mobile screen -->
<div class="page" style="left:965px;top:644px;width:129px;height:236px;box-shadow:0 0 0 1px #d8d8d8">
  <div class="brandmark" style="left:10px;top:5px;gap:3px"><span class="name" style="font-size:7px">Bork Ventures</span><span class="box" style="width:5px;height:5px"></span></div>
  <div class="abs" style="left:0;top:18px;width:129px;height:14px;background:var(--brand)"></div>
  <div class="photo" role="img" aria-label="Network switch with patch cables" style="left:0;top:32px;width:129px;height:70px;background:linear-gradient(135deg,#8b9185,#cfd2c6 40%,#3a403a)"></div>
  <div class="abs head" style="left:68px;top:58px;font-size:9px;color:var(--brand)">Leadership</div>
  <div class="abs head center" style="left:0;width:129px;top:112px;font-size:8px">Our Services</div>
  <svg class="abs" style="left:55px;top:130px" width="20" height="20" viewBox="0 0 20 20"><rect x="3" y="3" width="14" height="10" fill="none" stroke="#444"/><circle cx="15" cy="4" r="3" fill="var(--brand)"/></svg>
  <div class="abs center tiny" style="left:10px;width:109px;top:156px;font-size:4px;line-height:6px">Hardware / Software Sales<br>Reliable sourcing from leading<br>makers across the region.</div>
  <div class="btn" style="left:52px;top:182px;width:24px;height:7px;font-size:3.5px;line-height:7px">Read More</div>
</div>

<!-- ============ SECTION LABELS ============ -->
<div class="section-tag" style="left:76px;top:1045px;width:269px;height:49px">Desktop Version</div>
<div class="section-tag" style="left:789px;top:1045px;width:269px;height:49px">Mobile Responsive</div>

<!-- ============ DESKTOP PAGE ============ -->
<div class="page" style="left:74px;top:1124px;width:650px;height:2043px">
  <!-- header -->
  <div class="brandmark" style="left:49px;top:12px;gap:4px"><span class="name" style="font-size:11px">Bork Ventures</span><span class="box" style="width:8px;height:8px"></span></div>
  <div class="tagline" style="left:140px;top:13px;font-size:8px">Insight Trust Outcomes</div>
  <div class="abs" style="left:433px;top:5px;font-size:5.5px;color:#555"><span style="color:var(--brand)">&#9679;</span> Call Us: 555-014-2290 &nbsp;<span style="color:var(--brand)">&#9679;</span> Mail Us: info@borkventuresinc.example</div>
  <div class="nav" style="left:344px;top:27px;gap:19px"><span class="on">Home</span><span>About Us</span><span>Services</span><span>Strategy</span><span>IT News</span><span>Contact Us</span></div>

  <!-- hero -->
  <div class="photo" role="img" aria-label="Close-up photo of a network switch with patch cables" style="left:0;top:46px;width:650px;height:280px;background:linear-gradient(135deg,#7e857a 0%,#cdd0c4 30%,#8a8f83 55%,#2b312c 100%)"></div>
  <div class="abs head" style="left:395px;top:140px;font-size:12px;color:#fff;font-weight:600">Bringing Thought</div>
  <div class="abs head" style="left:395px;top:156px;font-size:36px;color:var(--brand);line-height:38px">Leadership</div>
  <div class="abs head" style="left:395px;top:198px;font-size:9px;color:#fff;letter-spacing:3px;font-weight:600">— Quality to every project</div>

  <!-- services -->
  <div class="abs" style="left:0;top:326px;width:650px;height:282px;background:#fbfbfb"></div>
  <div class="abs head center" style="left:0;width:650px;top:380px;font-size:17px">Our Services</div>

  <svg class="abs" style="left:101px;top:424px" width="32" height="34" viewBox="0 0 32 34"><rect x="5" y="6" width="20" height="16" fill="none" stroke="#444" stroke-width="1.3"/><rect x="9" y="10" width="12" height="8" fill="none" stroke="#444"/><path d="M4 28h24" stroke="var(--brand)" stroke-width="2"/><circle cx="26" cy="7" r="5" fill="#e6b12e"/></svg>
  <svg class="abs" style="left:239px;top:424px" width="32" height="34" viewBox="0 0 32 34"><circle cx="16" cy="9" r="6" fill="#333"/><path d="M5 30c0-8 5-12 11-12s11 4 11 12z" fill="#333"/><path d="M16 18l-2 8h4z" fill="var(--brand)"/><circle cx="26" cy="6" r="4" fill="#e6b12e"/></svg>
  <svg class="abs" style="left:376px;top:424px" width="32" height="34" viewBox="0 0 32 34"><circle cx="16" cy="13" r="8" fill="none" stroke="#444" stroke-width="1.3"/><rect x="12" y="22" width="8" height="5" fill="none" stroke="#444"/><path d="M16 1v3M4 13H1M31 13h-3M7 4l2 2M25 4l-2 2" stroke="#e6b12e" stroke-width="1.5"/><path d="M10 30h12" stroke="var(--brand)" stroke-width="2"/></svg>
  <svg class="abs" style="left:514px;top:424px" width="32" height="34" viewBox="0 0 32 34"><circle cx="16" cy="15" r="7" fill="none" stroke="#444" stroke-width="1.3"/><circle cx="16" cy="15" r="3" fill="var(--brand)"/><path d="M16 4v4M16 22v4M5 15h4M23 15h4M8 7l3 3M24 7l-3 3M8 23l3-3M24 23l-3-3" stroke="#444" stroke-width="1.5"/></svg>

  <div class="abs center" style="left:57px;width:120px;top:483px;font-size:7px;color:#333">Hardware / Software Sales</div>
  <div class="abs center" style="left:195px;width:120px;top:483px;font-size:7px;color:#333">Professional Services</div>
  <div class="abs center" style="left:332px;width:120px;top:483px;font-size:7px;color:#333">Technology Assessment</div>
  <div class="abs center" style="left:470px;width:120px;top:483px;font-size:7px;color:#333">Technology Consulting</div>

  <p class="abs center tiny" style="left:57px;width:120px;top:496px">We source hardware and software from leading makers across the region and keep strong ties with them.</p>
  <p class="abs center tiny" style="left:195px;width:120px;top:496px">Our team brings seasoned staff with deep know-how to help you shape the right plan for your goals.</p>
  <p class="abs center tiny" style="left:332px;width:120px;top:496px">We review your current systems, find the gaps and help you pick the right path for growth.</p>
  <p class="abs center tiny" style="left:470px;width:120px;top:496px">Sound advice on applying modern tools to real problems, backed by broad field experience.</p>

  <div class="btn" style="left:102px;top:547px;width:32px;height:9px;font-size:4.5px;line-height:9px">Read More</div>
  <div class="btn" style="left:239px;top:547px;width:32px;height:9px;font-size:4.5px;line-height:9px">Read More</div>
  <div class="btn" style="left:376px;top:547px;width:32px;height:9px;font-size:4.5px;line-height:9px">Read More</div>
  <div class="btn" style="left:514px;top:547px;width:32px;height:9px;font-size:4.5px;line-height:9px">Read More</div>

  <!-- about -->
  <div class="abs" style="left:0;top:608px;width:650px;height:195px;background:var(--panel)"></div>
  <div class="photo" role="img" aria-label="Photo of an engineer working at a server rack" style="left:0;top:608px;width:310px;height:195px;background:linear-gradient(120deg,#0d1a2a 0%,#29445f 45%,#5d7a93 100%)"></div>
  <svg class="abs" style="left:255px;top:608px" width="60" height="195" viewBox="0 0 60 195"><polygon points="0,0 25,0 55,40 55,195 40,195 40,45" fill="var(--brand)"/></svg>
  <div class="abs head" style="left:341px;top:625px;font-size:9px;font-weight:500;color:#666">About Our</div>
  <div class="abs head" style="left:341px;top:640px;font-size:17px">Bork Ventures</div>
  <p class="abs tiny" style="left:341px;top:668px;width:262px">Bork Ventures, Inc. is an 8(a) innovative and rapidly growing full-service IT consulting firm. We provide our clients with modern technology solutions and the know-how to apply them to their own business models.<br>For over 20 years, we have been providing reliable IT solutions to businesses in the wider metro area. Our full range of services gives clients tailored technology solutions shaped to meet the specific demands of their business.</p>
  <div class="btn" style="left:341px;top:776px;width:36px;height:9px;font-size:4.5px;line-height:9px">Read More</div>

  <!-- leaders -->
  <div class="abs head center" style="left:0;width:650px;top:858px;font-size:17px">Our Leaders</div>
  <div class="photo" role="img" aria-label="Portrait photo of the co-founder" style="left:301px;top:888px;width:49px;height:72px;background:linear-gradient(180deg,#e4e4e4,#8c8c8c)"></div>
  <div class="abs center" style="left:0;width:650px;top:972px;font-size:7px;color:#333"><b style="font-family:'Rajdhani',sans-serif">RAVI KOSHAL</b> – CO-FOUNDER</div>
  <p class="abs center tiny" style="left:110px;width:430px;top:985px">Ravi has played a leading role in the IT field for more than 20 years, running divisions and business units. Since founding Bork Ventures in 2005, he has been key in shaping the company's strategy and building the team and culture that guide its work.</p>
  <div class="btn" style="left:309px;top:1033px;width:34px;height:9px;font-size:4.5px;line-height:9px">Read More</div>
  <div class="abs" style="left:318px;top:1055px;width:4px;height:4px;border-radius:50%;background:#333"></div>
  <div class="abs" style="left:325px;top:1055px;width:4px;height:4px;border-radius:50%;background:#bbb"></div>

  <!-- strategy -->
  <svg class="abs" style="left:0;top:1072px" width="650" height="322" viewBox="0 0 650 322">
    <polygon points="0,0 0,322 650,322 650,0 330,60" fill="#f7f7f7"/>
    <polyline points="0,0 330,60 650,0" fill="none" stroke="var(--brand)" stroke-width="4"/>
    <polyline points="0,12 330,70 650,12" fill="none" stroke="var(--brand)" stroke-width="1"/>
  </svg>
  <div class="photo" role="img" aria-label="Photo of a technician with a laptop in a server room" style="left:310px;top:1130px;width:340px;height:250px;clip-path:polygon(30% 0,100% 0,100% 100%,0 100%);background:linear-gradient(110deg,#dfe6ef 0%,#7f99b8 45%,#213f66 100%)"></div>
  <div class="abs head" style="left:50px;top:1140px;font-size:9px;font-weight:500;color:#666">Our Strategy</div>
  <div class="abs head" style="left:50px;top:1156px;font-size:17px">Your Path to Success</div>
  <p class="abs tiny" style="left:50px;top:1184px;width:250px">Civilian and federal agencies face rising demands driven by a changing economic setting and shifts in how goods and services are sold and delivered. These forces make it vital to use new and better technology, and modern IT solutions can help lower cost and lift delivery. Many agencies now face a key test: making tech work as a lasting edge, with more firms than ever keen to stay ahead of the field.</p>
  <div class="btn" style="left:50px;top:1307px;width:36px;height:9px;font-size:4.5px;line-height:9px">Read More</div>

  <!-- news -->
  <div class="abs head center" style="left:0;width:650px;top:1420px;font-size:17px">Latest IT News</div>
  <div class="photo" role="img" aria-label="Photo of a hand holding a smartphone beside a router" style="left:49px;top:1458px;width:176px;height:129px;background:linear-gradient(160deg,#f1f1ef,#b9b7ae 60%,#6b6a63)"></div>
  <div class="photo" role="img" aria-label="Photo of a hand signing a document" style="left:236px;top:1458px;width:176px;height:129px;background:linear-gradient(160deg,#fafafa,#cfcfcc 60%,#85847f)"></div>
  <div class="photo" role="img" aria-label="Photo of a businessman with a tablet in a data centre" style="left:422px;top:1458px;width:176px;height:129px;background:linear-gradient(160deg,#c9d6e6,#5e7da4 55%,#1f3657)"></div>

  <div class="abs" style="left:49px;top:1594px;font-size:5.5px;color:#999">17TH AUGUST, 2019</div>
  <div class="abs" style="left:236px;top:1594px;font-size:5.5px;color:#999">17TH AUGUST, 2019</div>
  <div class="abs" style="left:422px;top:1594px;font-size:5.5px;color:#999">17TH AUGUST, 2019</div>
  <div class="abs" style="left:49px;top:1609px;width:176px;font-size:9px;line-height:11px;color:#333">There are many variations of passages of Lorem Ipsum</div>
  <div class="abs" style="left:236px;top:1609px;width:176px;font-size:9px;line-height:11px;color:#333">There are many variations of passages of Lorem Ipsum</div>
  <div class="abs" style="left:422px;top:1609px;width:176px;font-size:9px;line-height:11px;color:#333">There are many variations of passages of Lorem Ipsum</div>
  <p class="abs tiny" style="left:49px;top:1642px;width:150px">If you use this site regularly and would like to help keep the site on the web, please consider a small sum.</p>
  <p class="abs tiny" style="left:236px;top:1642px;width:150px">If you use this site regularly and would like to help keep the site on the web, please consider a small sum.</p>
  <p class="abs tiny" style="left:422px;top:1642px;width:150px">If you use this site regularly and would like to help keep the site on the web, please consider a small sum.</p>
  <div class="btn" style="left:49px;top:1684px;width:34px;height:9px;font-size:4.5px;line-height:9px">Read More</div>
  <div class="btn" style="left:236px;top:1684px;width:34px;height:9px;font-size:4.5px;line-height:9px">Read More</div>
  <div class="btn" style="left:422px;top:1684px;width:34px;height:9px;font-size:4.5px;line-height:9px">Read More</div>

  <!-- footer -->
  <div class="footer" style="top:1750px;width:650px;height:293px">
    <svg class="abs" style="left:113px;top:26px" width="12" height="14" viewBox="0 0 12 14"><path d="M6 0a5 5 0 0 0-5 5c0 4 5 9 5 9s5-5 5-9a5 5 0 0 0-5-5z" fill="#fff"/><circle cx="6" cy="5" r="2" fill="var(--footer)"/></svg>
    <svg class="abs" style="left:251px;top:26px" width="12" height="14" viewBox="0 0 12 14"><path d="M2 1l3 0 1 3-2 1.5c1 2 2 3 4 4L9.5 7.5l3 1V12c-6 1-12-5-11-11z" fill="#fff"/></svg>
    <svg class="abs" style="left:389px;top:28px" width="13" height="10" viewBox="0 0 13 10"><rect width="13" height="10" fill="#fff"/><path d="M0 0l6.5 5L13 0" fill="none" stroke="var(--footer)"/></svg>
    <svg class="abs" style="left:526px;top:26px" width="14" height="13" viewBox="0 0 14 13"><ellipse cx="7" cy="5.5" rx="7" ry="5.5" fill="var(--brand)"/><path d="M3 9l-1 4 4-2.5z" fill="var(--brand)"/></svg>
    <div class="abs center" style="left:59px;width:120px;top:45px;font-size:6px;line-height:8px">2201 Harlow Bend Dr Fenwick,<br>MD 20000</div>
    <div class="abs center" style="left:197px;width:120px;top:50px;font-size:6px">555-014-2290</div>
    <div class="abs center" style="left:325px;width:140px;top:50px;font-size:6px">info@borkventuresinc.example</div>
    <div class="abs center" style="left:472px;width:120px;top:50px;font-size:6px">Live Chat</div>

    <div class="foot-head" style="left:49px;top:86px;font-size:8px">Quick Links</div>
    <div class="foot-head" style="left:206px;top:86px;font-size:8px">Services</div>
    <div class="foot-head" style="left:373px;top:86px;font-size:8px">IT Strategy</div>
    <div class="foot-head" style="left:501px;top:86px;font-size:8px">Newsletter</div>
    <ul class="foot-list tiny" style="left:49px;top:102px;line-height:14px"><li>Home</li><li>About us</li><li>Services</li><li>Strategy</li><li>IT News</li><li>Contact us</li></ul>
    <ul class="foot-list tiny" style="left:206px;top:102px;line-height:14px"><li>Hardware / Software Sales</li><li>Professional Services</li><li>Technology Assessment</li><li>Technology Consulting</li></ul>
    <ul class="foot-list tiny" style="left:373px;top:102px;line-height:14px"><li>Assess</li><li>Recommend</li><li>Implement</li><li>Monitor</li><li>Manage</li></ul>
    <div class="field tiny" style="left:501px;top:106px;width:97px;height:14px;line-height:12px">Enter Name</div>
    <div class="field tiny" style="left:501px;top:125px;width:97px;height:14px;line-height:12px">Enter Email</div>
    <div class="btn" style="left:501px;top:144px;width:97px;height:12px;font-size:5px;line-height:12px">Subscribe</div>

    <div class="abs" style="left:49px;top:224px;width:552px;height:1px;background:#3a3d42"></div>
    <div class="social" style="left:51px;top:225px;width:134px;height:23px;font-size:7px;line-height:23px">&#9679; Friendwall</div>
    <div class="social-word" style="left:196px;width:120px;top:232px;font-size:7px">Chirpline</div>
    <div class="social-word" style="left:333px;width:120px;top:232px;font-size:7px">Blog</div>
    <div class="social-word" style="left:472px;width:120px;top:232px;font-size:7px">Prolink</div>
    <div class="abs center" style="left:0;width:650px;top:268px;font-size:5px;color:#8d9095">COPYRIGHT © 2019 <b style="color:#fff">BORK VENTURES</b>. ALL RIGHTS RESERVED.</div>
  </div>
</div>

<!-- ============ MOBILE PAGE ============ -->
<div class="page" style="left:793px;top:1124px;width:241px;height:3472px">
  <div class="brandmark" style="left:22px;top:9px;gap:4px"><span class="name" style="font-size:12px">Bork Ventures</span><span class="box" style="width:8px;height:8px"></span></div>
  <div class="tagline" style="left:128px;top:11px;font-size:8px">Insight Trust Outcomes</div>
  <div class="abs" style="left:0;top:35px;width:241px;height:30px;background:var(--brand)"></div>
  <svg class="abs" style="left:14px;top:44px" width="16" height="12" viewBox="0 0 16 12"><path d="M0 1h16M0 6h16M0 11h16" stroke="#fff" stroke-width="1.6"/></svg>
  <svg class="abs" style="left:209px;top:42px" width="16" height="16" viewBox="0 0 16 16"><circle cx="8" cy="8" r="8" fill="#fff"/><path d="M5 5l2 0 1 2-1 1c.5 1 1 1.5 2 2l1-1 2 1v2c-4 0-7-3-7-7z" fill="var(--brand)"/></svg>
  <div class="photo" role="img" aria-label="Close-up photo of a network switch with patch cables" style="left:0;top:65px;width:241px;height:140px;background:linear-gradient(135deg,#7e857a 0%,#cdd0c4 35%,#6f7468 60%,#2b312c 100%)"></div>
  <div class="abs head" style="left:150px;top:120px;font-size:6px;color:#fff">Bringing Thought</div>
  <div class="abs head" style="left:150px;top:127px;font-size:16px;color:var(--brand)">Leadership</div>
  <div class="abs head" style="left:150px;top:145px;font-size:4.5px;color:#fff;letter-spacing:1px">Quality to every project</div>

  <div class="abs head center" style="left:0;width:241px;top:222px;font-size:15px">Our Services</div>

  <svg class="abs" style="left:105px;top:262px" width="32" height="34" viewBox="0 0 32 34"><rect x="5" y="6" width="20" height="16" fill="none" stroke="#444" stroke-width="1.3"/><rect x="9" y="10" width="12" height="8" fill="none" stroke="#444"/><path d="M4 28h24" stroke="var(--brand)" stroke-width="2"/><circle cx="26" cy="7" r="5" fill="#e6b12e"/></svg>
  <div class="abs center" style="left:0;width:241px;top:319px;font-size:7.5px;color:#333">Hardware / Software Sales</div>
  <p class="abs center tiny" style="left:45px;width:151px;top:333px">We source hardware and software from leading makers across the region and keep strong ties with many of them.</p>
  <div class="btn" style="left:102px;top:388px;width:38px;height:10px;font-size:5px;line-height:10px">Read More</div>

  <svg class="abs" style="left:105px;top:420px" width="32" height="34" viewBox="0 0 32 34"><circle cx="16" cy="9" r="6" fill="#333"/><path d="M5 30c0-8 5-12 11-12s11 4 11 12z" fill="#333"/><path d="M16 18l-2 8h4z" fill="var(--brand)"/><circle cx="26" cy="6" r="4" fill="#e6b12e"/></svg>
  <div class="abs center" style="left:0;width:241px;top:474px;font-size:7.5px;color:#333">Professional Services</div>
  <p class="abs center tiny" style="left:45px;width:151px;top:488px">Our team brings seasoned staff with deep know-how to help you shape the right plan for your goals and needs.</p>
  <div class="btn" style="left:102px;top:545px;width:38px;height:10px;font-size:5px;line-height:10px">Read More</div>

  <svg class="abs" style="left:105px;top:577px" width="32" height="34" viewBox="0 0 32 34"><circle cx="16" cy="13" r="8" fill="none" stroke="#444" stroke-width="1.3"/><rect x="12" y="22" width="8" height="5" fill="none" stroke="#444"/><path d="M16 1v3M4 13H1M31 13h-3M7 4l2 2M25 4l-2 2" stroke="#e6b12e" stroke-width="1.5"/><path d="M10 30h12" stroke="var(--brand)" stroke-width="2"/></svg>
  <div class="abs center" style="left:0;width:241px;top:635px;font-size:7.5px;color:#333">Technology Assessment</div>
  <p class="abs center tiny" style="left:45px;width:151px;top:649px">We review your current systems, find the gaps and help you pick the right path for steady growth.</p>
  <div class="btn" style="left:102px;top:706px;width:38px;height:10px;font-size:5px;line-height:10px">Read More</div>

  <svg class="abs" style="left:105px;top:743px" width="32" height="34" viewBox="0 0 32 34"><circle cx="16" cy="15" r="7" fill="none" stroke="#444" stroke-width="1.3"/><circle cx="16" cy="15" r="3" fill="var(--brand)"/><path d="M16 4v4M16 22v4M5 15h4M23 15h4M8 7l3 3M24 7l-3 3M8 23l3-3M24 23l-3-3" stroke="#444" stroke-width="1.5"/></svg>
  <div class="abs center" style="left:0;width:241px;top:798px;font-size:7.5px;color:#333">Technology Consulting</div>
  <p class="abs center tiny" style="left:45px;width:151px;top:812px">Sound advice on applying modern tools to real problems, backed by broad field experience and trusted skill.</p>
  <div class="btn" style="left:102px;top:867px;width:38px;height:10px;font-size:5px;line-height:10px">Read More</div>

  <div class="photo" role="img" aria-label="Photo of an engineer working at a server rack" style="left:8px;top:911px;width:227px;height:148px;background:linear-gradient(120deg,#0d1a2a 0%,#29445f 45%,#5d7a93 100%)"></div>
  <div class="abs head center" style="left:0;width:241px;top:1085px;font-size:8px;font-weight:500;color:#666">About Our</div>
  <div class="abs head center" style="left:0;width:241px;top:1100px;font-size:15px">Bork Ventures</div>
  <p class="abs center tiny" style="left:8px;width:225px;top:1123px;line-height:10.5px">Bork Ventures, Inc. is an 8(a) innovative and rapidly growing full-service IT consulting firm. We provide our clients with modern technology solutions and the know-how to apply them to their own business models.<br>For over 20 years, we have been providing reliable IT solutions to businesses in the wider metro area. Our full range of services gives clients tailored technology solutions shaped to meet the specific demands of their business.</p>
  <div class="btn" style="left:83px;top:1273px;width:75px;height:22px;font-size:7px;line-height:22px">Read More</div>

  <div class="abs head center" style="left:0;width:241px;top:1341px;font-size:15px">Our Leaders</div>
  <div class="photo" role="img" aria-label="Portrait photo of the co-founder" style="left:97px;top:1371px;width:48px;height:70px;background:linear-gradient(180deg,#e4e4e4,#8c8c8c)"></div>
  <div class="abs center" style="left:0;width:241px;top:1449px;font-size:7.5px;color:#333"><b style="font-family:'Rajdhani',sans-serif">RAVI KOSHAL</b> – CO-FOUNDER</div>
  <p class="abs center tiny" style="left:20px;width:201px;top:1467px;line-height:10.5px">Ravi has played a leading role in the IT field for more than 20 years, running divisions and business units. Since founding Bork Ventures in 2005, he has been key in shaping the company's strategy and building the team and culture that guide its work.</p>
  <div class="btn" style="left:83px;top:1576px;width:75px;height:20px;font-size:7px;line-height:20px">Read More</div>
  <div class="abs" style="left:113px;top:1615px;width:4px;height:4px;border-radius:50%;background:#333"></div>
  <div class="abs" style="left:120px;top:1615px;width:4px;height:4px;border-radius:50%;background:#bbb"></div>

  <div class="photo" role="img" aria-label="Photo of a technician with a laptop in a server room" style="left:6px;top:1636px;width:235px;height:150px;background:linear-gradient(110deg,#dfe6ef 0%,#7f99b8 45%,#213f66 100%)"></div>
  <div class="abs head center" style="left:0;width:241px;top:1800px;font-size:8px;font-weight:500;color:#666">Our Strategy</div>
  <div class="abs head center" style="left:0;width:241px;top:1815px;font-size:15px">Your Path to Success</div>
  <p class="abs center tiny" style="left:8px;width:225px;top:1840px;line-height:11px">Civilian and federal agencies face rising demands driven by a changing economic setting and shifts in how goods and services are sold and delivered. These forces make it vital to use new and better technology, and modern IT solutions can help lower cost and lift delivery. Many agencies now face a key test: making tech work as a lasting edge, with more firms than ever keen to stay ahead of the field and win.</p>

  <div class="abs head center" style="left:0;width:241px;top:2055px;font-size:15px">Latest IT News</div>
  <div class="photo" role="img" aria-label="Photo of a hand holding a smartphone beside a router" style="left:8px;top:2088px;width:226px;height:163px;background:linear-gradient(160deg,#f1f1ef,#b9b7ae 60%,#6b6a63)"></div>
  <div class="abs center" style="left:0;width:241px;top:2266px;font-size:5.5px;color:#999">17TH AUGUST, 2019</div>
  <div class="abs center" style="left:8px;width:225px;top:2281px;font-size:10px;line-height:12px;color:#333">There are many variations of passages<br>of Lorem Ipsum</div>
  <p class="abs center tiny" style="left:8px;width:225px;top:2327px">If you use this site regularly and would like to help keep the site on the web, please consider a small sum.</p>
  <div class="btn" style="left:103px;top:2364px;width:36px;height:10px;font-size:5px;line-height:10px">Read More</div>
  <svg class="abs" style="left:94px;top:2395px" width="54" height="22" viewBox="0 0 54 22"><circle cx="11" cy="11" r="10" fill="#fff" stroke="#ccc"/><path d="M13 7l-4 4 4 4" fill="none" stroke="#999" stroke-width="1.5"/><circle cx="43" cy="11" r="10" fill="var(--brand)"/><path d="M41 7l4 4-4 4" fill="none" stroke="#fff" stroke-width="1.5"/></svg>

  <div class="footer" style="top:2441px;width:241px;height:1031px">
    <svg class="abs" style="left:115px;top:14px" width="12" height="14" viewBox="0 0 12 14"><path d="M6 0a5 5 0 0 0-5 5c0 4 5 9 5 9s5-5 5-9a5 5 0 0 0-5-5z" fill="#fff"/><circle cx="6" cy="5" r="2" fill="var(--footer)"/></svg>
    <div class="abs center" style="left:0;width:241px;top:32px;font-size:6px;line-height:8px">2201 Harlow Bend Dr Fenwick,<br>MD 20000</div>
    <svg class="abs" style="left:115px;top:71px" width="12" height="14" viewBox="0 0 12 14"><path d="M2 1l3 0 1 3-2 1.5c1 2 2 3 4 4L9.5 7.5l3 1V12c-6 1-12-5-11-11z" fill="#fff"/></svg>
    <div class="abs center" style="left:0;width:241px;top:94px;font-size:6px">555-014-2290</div>
    <svg class="abs" style="left:114px;top:128px" width="13" height="10" viewBox="0 0 13 10"><rect width="13" height="10" fill="#fff"/><path d="M0 0l6.5 5L13 0" fill="none" stroke="var(--footer)"/></svg>
    <div class="abs center" style="left:0;width:241px;top:149px;font-size:6px">info@borkventuresinc.example</div>
    <svg class="abs" style="left:113px;top:180px" width="14" height="13" viewBox="0 0 14 13"><ellipse cx="7" cy="5.5" rx="7" ry="5.5" fill="var(--brand)"/><path d="M3 9l-1 4 4-2.5z" fill="var(--brand)"/></svg>
    <div class="abs center" style="left:0;width:241px;top:207px;font-size:7px">Live Chat</div>

    <div class="foot-head" style="left:7px;top:251px;font-size:9px">Quick Links</div>
    <ul class="foot-list" style="left:7px;top:270px;font-size:6.5px;line-height:19.7px"><li>Home</li><li>About us</li><li>Services</li><li>Strategy</li><li>IT News</li><li>Contact us</li></ul>
    <div class="foot-head" style="left:7px;top:402px;font-size:9px">Services</div>
    <ul class="foot-list" style="left:7px;top:422px;font-size:6.5px;line-height:19.7px"><li>Hardware / Software Sales</li><li>Professional Services</li><li>Technology Assessment</li><li>Technology Consulting</li></ul>
    <div class="foot-head" style="left:7px;top:518px;font-size:9px">IT Strategy</div>
    <ul class="foot-list" style="left:7px;top:540px;font-size:6.5px;line-height:20.5px"><li>Assess</li><li>Recommend</li><li>Implement</li><li>Monitor</li><li>Manage</li></ul>
    <div class="foot-head" style="left:7px;top:661px;font-size:9px">Newsletter</div>
    <div class="field" style="left:7px;top:680px;width:227px;height:24px;line-height:22px;font-size:6px">Enter Name</div>
    <div class="field" style="left:7px;top:715px;width:227px;height:24px;line-height:22px;font-size:6px">Enter Email</div>
    <div class="btn" style="left:7px;top:747px;width:227px;height:25px;font-size:8px;line-height:25px">Subscribe</div>
    <div class="social" style="left:7px;top:788px;width:227px;height:37px;font-size:9px;line-height:37px">&#9679; Friendwall</div>
    <div class="social-word" style="left:0;width:241px;top:841px;font-size:9px">Chirpline</div>
    <div class="social-word" style="left:0;width:241px;top:880px;font-size:9px">Blog</div>
    <div class="social-word" style="left:0;width:241px;top:918px;font-size:9px">Prolink</div>
    <div class="abs center" style="left:0;width:241px;top:954px;font-size:5.5px;color:#8d9095">Copyright © 2019 <b style="color:#fff">Bork Ventures</b>. All rights reserved.</div>
  </div>
</div>

<!-- ============ THANK YOU ============ -->
<svg class="thanks" width="710" height="380" viewBox="0 0 710 380" aria-label="Thank you">
  <text x="0" y="168" textLength="700" lengthAdjust="spacingAndGlyphs" font-family="'Archivo Black', sans-serif" font-size="200" fill="var(--thanks)">THANK</text>
  <text x="120" y="358" textLength="480" lengthAdjust="spacingAndGlyphs" font-family="'Archivo Black', sans-serif" font-size="200" fill="var(--thanks)">YOU</text>
</svg>

</body>
</html>
```